QAMBRO THERAPEUTICS

physical therapy company. need a flashy image and named logo, website link, that I can also use on Letterhead and business cards. Clean, sharp, modern, eye catching. 3 colors? Some shine. Needs to stand out and not be trendy or too much cursive . Androgynous image of a human body is ok. A spine included is ok. Prefer lines to curves for font types. Warm colors but strong impact. Will need to have some contact info and border mission statement on it.
Updates

Target Market(s)

Target market is large corporations, wealthy individuals, medical doctors

Industry/Entity Type

Medical, physical therapy

Contact Information for Business Card

Name, Owner, phone, email, and website

Colors
0054AA
0677BA
7BADD7
CADEEF
E8F1F8

Requirements
Must have
• See above- something about BALANCE, wellness, strength etc
Nice to have
• Contrast, depth
Should not have
• No cursive

```html
<!DOCTYPE html>
<html lang="en">
<head>
<meta charset="UTF-8">
<title>Qambro Therapeutics – Business Card</title>
<link href="https://fonts.googleapis.com/css2?family=Cinzel:wght@600;700&family=Poppins:wght@400;500&display=swap" rel="stylesheet">
<style>
  :root {
    --brand-blue: #0054aa;
    --card-blue: #1a5fbf;
    --ink: #1d1d1f;
    --paper: #f4f5f7;
    --paper-shade: #e4e7ec;
    --silver: #d9dee6;
    --backdrop: #2b2b2e;
    --photo-light: #f2f5f9;
    --photo-mid: #c9d9ec;
    --photo-deep: #7badd7;
  }
  * { margin: 0; padding: 0; box-sizing: border-box; }
  html, body { width: 1200px; height: 900px; overflow: hidden; }
  body {
    background: var(--backdrop);
    position: relative;
    font-family: "Poppins", sans-serif;
  }
  .card {
    position: absolute;
    left: 270px;
    width: 660px;
    height: 377px;
    border-radius: 22px;
    overflow: hidden;
    box-shadow: 0 14px 30px rgba(0,0,0,0.45);
  }
  /* Front */
  .card-front {
    top: 40px;
    background: linear-gradient(135deg, var(--paper) 0%, #ffffff 45%, var(--paper-shade) 100%);
  }
  .company-name {
    position: absolute;
    z-index: 2;
    left: 40px;
    top: 62px;
    font-family: "Cinzel", serif;
    font-weight: 700;
    font-size: 32px;
    letter-spacing: 0.5px;
    white-space: nowrap;
    color: var(--brand-blue);
  }
  .photo-area {
    position: absolute;
    z-index: 1;
    left: 380px;
    top: 128px;
    width: 280px;
    height: 215px;
    background:
      linear-gradient(90deg, rgba(255,255,255,0.95) 0%, rgba(255,255,255,0) 30%),
      linear-gradient(160deg, var(--photo-light) 0%, var(--photo-mid) 55%, var(--photo-deep) 100%);
  }
  .name-marker {
    position: absolute;
    z-index: 2;
    left: 26px;
    top: 218px;
    width: 20px;
    height: 46px;
    background: var(--brand-blue);
  }
  .person {
    position: absolute;
    z-index: 2;
    left: 62px;
    top: 212px;
  }
  .person-name {
    font-family: "Cinzel", serif;
    font-weight: 600;
    font-size: 23px;
    color: var(--brand-blue);
    line-height: 1.1;
    white-space: nowrap;
  }
  .person-role {
    font-size: 15px;
    color: var(--ink);
    line-height: 1.3;
  }
  .contact-list {
    position: absolute;
    z-index: 2;
    left: 62px;
    top: 270px;
    list-style: none;
    font-size: 15px;
    color: var(--ink);
    line-height: 1.3;
    white-space: nowrap;
  }
  .contact-list li { display: flex; align-items: center; gap: 9px; }
  .contact-list svg { width: 15px; height: 15px; fill: var(--brand-blue); flex: none; }
  .domain { color: var(--brand-blue); }
  .accent-band {
    position: absolute;
    z-index: 1;
    left: 0;
    top: 0;
    width: 660px;
    height: 377px;
  }
  /* Back */
  .card-back {
    top: 483px;
    background: linear-gradient(135deg, #2268c8 0%, var(--card-blue) 55%, #1553ad 100%);
    display: flex;
    align-items: center;
    justify-content: center;
  }
  .back-name {
    font-family: "Cinzel", serif;
    font-weight: 700;
    font-size: 34px;
    letter-spacing: 1px;
    color: var(--silver);
    white-space: nowrap;
  }
</style>
</head>
<body>
  <section class="card card-front">
    <h1 class="company-name">QAMBRO THERAPEUTICS</h1>
    <div class="photo-area" role="img" aria-label="Photo of a physical therapist guiding a patient's arm and shoulder, with a spine model in the background"></div>
    <svg class="accent-band" viewBox="0 0 660 377" aria-hidden="true">
      <polygon points="0,366 660,300 660,377 0,377" fill="var(--brand-blue)"/>
    </svg>
    <div class="name-marker"></div>
    <div class="person">
      <p class="person-name">DANIEL HARGROVE</p>
      <p class="person-role">Managing Director</p>
    </div>
    <ul class="contact-list">
      <li>
        <svg viewBox="0 0 24 24"><path d="M6.6 10.8a15.1 15.1 0 0 0 6.6 6.6l2.2-2.2a1 1 0 0 1 1-.25 11.4 11.4 0 0 0 3.6.57 1 1 0 0 1 1 1V20a1 1 0 0 1-1 1A17 17 0 0 1 3 4a1 1 0 0 1 1-1h3.5a1 1 0 0 1 1 1c0 1.25.2 2.45.57 3.57a1 1 0 0 1-.25 1z"/></svg>
        044-987 654 321
      </li>
      <li>
        <svg viewBox="0 0 24 24"><path d="M2 5h20v14H2z" fill="none" stroke="var(--brand-blue)" stroke-width="2"/><path d="M2 5l10 8 10-8" fill="none" stroke="var(--brand-blue)" stroke-width="2"/></svg>
        info@qambrocare.com
      </li>
      <li>
        <svg viewBox="0 0 24 24"><g fill="none" stroke="var(--brand-blue)" stroke-width="2"><circle cx="12" cy="12" r="9.5"/><ellipse cx="12" cy="12" rx="4" ry="9.5"/><path d="M2.5 12h19M4 7h16M4 17h16"/></g></svg>
        <span>www.<span class="domain">qambrocare</span>.com</span>
      </li>
    </ul>
  </section>

  <section class="card card-back">
    <p class="back-name">QAMBRO THERAPEUTICS</p>
  </section>
</body>
</html>
```